CrestHornSupply.com

I need a new webdesign for a company in the San Jose/SF Bay area that showcases the financial benefits of buying used band instruments for junior high students.This would be opposed to the current and costly option of renting cheap quality instruments from the 2 or 3 local music stores that charge a monthly fee that over the years charges the buyer 3 or 4x over..
Instruments: focus in on Alto Sax, Trumpet, Flute, Clarinet, Trombone, Tenor Sax, Baritone
Target middle schools are Larkfield Middle School and Maple Middle School in San Jose, CA. Both have award winning band programs.
Files attached may or may not be important.
Tabs Needed and funtional
Contact
Shopping Cart
Select Instrument
Checkout
Add to Cart, etc.
Instuments
quantity, etc.
trade in your instrument/sell your instrument
ability to add or take away new instruments for sale. including pictures
Additional questions or info, feel free to ask
Updates
Hi Designers,
Project Deadline Extended
Reason: In the next week you will be receiving specific content that will be required to be had on the website.
New desigins are still welcome. Please continue to contact me if you have questions about your individual designs.
Thanks!
Crest Horn

```html
<!DOCTYPE html>
<html lang="en">
<head>
<meta charset="utf-8">
<title>Crest Horn Instruments</title>
<link href="https://fonts.googleapis.com/css2?family=Open+Sans:wght@300;400;600&display=swap" rel="stylesheet">
<style>
:root{
  --gold:#f6c23b;
  --gold-dark:#c9961b;
  --brass:#c9962f;
  --brass-light:#efd488;
  --charcoal:#3f3f41;
  --ink:#222;
  --muted:#555;
  --rule:#d8d8d8;
  --bg:#f2f2f2;
  --white:#fff;
  --green:#3aa63a;
  --red:#e0263a;
  --link:#1a9bc7;
  --icon:#6b6b6b;
}
*{box-sizing:border-box;margin:0;padding:0}
html,body{width:1068px;height:1200px;overflow:hidden}
body{background:var(--bg);font-family:"Open Sans",Arial,sans-serif;color:var(--ink);position:relative}
.page{position:absolute;left:162px;top:121px;width:744px;height:1058px;background:var(--white);box-shadow:0 1px 4px rgba(0,0,0,.15)}
.abs{position:absolute}
.account-links{left:820px;top:10px;font-size:8px;color:var(--ink)}
.brand{left:162px;top:32px;display:flex;align-items:center;gap:8px}
.brand-mark{width:14px;height:14px;background:var(--gold)}
.brand-name{font-size:20px;font-weight:600;color:var(--charcoal);letter-spacing:.5px}
.pill{background:var(--gold);border-radius:6px;font-size:8.5px;font-weight:600;color:var(--ink);padding:0 8px;height:20px;line-height:20px;display:flex;align-items:center;gap:5px}
.pill-post{left:369px;top:35px}
.pill-gift{left:369px;top:62px}
.search{left:563px;top:61px;width:200px;height:21px;border:1px solid #ddd;border-radius:11px;font-size:7px;color:#999;padding-left:11px;line-height:19px;background:var(--white)}
.search-btn{position:absolute;right:-1px;top:-1px;width:26px;height:21px;background:var(--gold);border-radius:0 11px 11px 0}
.cart{left:790px;top:63px;font-size:11px;line-height:14px;white-space:nowrap}
.cart svg{vertical-align:-1px;margin-right:4px}
.cart b{color:var(--red);font-weight:400}
.bag{left:858px;top:61px;width:54px;height:21px;border-radius:6px;background:var(--gold);font-size:8.5px;font-weight:600;text-align:center;line-height:21px}
.nav{left:156px;top:95px;width:756px;height:26px;background:var(--gold);display:flex;align-items:center;font-size:9px;color:var(--ink)}
.nav a{padding:0 10px;border-right:1px solid var(--gold-dark);line-height:26px;color:inherit;text-decoration:none}
.nav .social{margin-left:auto;display:flex;gap:8px;padding-right:18px}
.dot-icon{width:10px;height:10px;border-radius:50%;background:var(--charcoal);display:inline-block}
.hero{left:162px;top:127px;width:744px;height:282px;overflow:hidden;background:var(--charcoal)}
.hero-photo{position:absolute;left:0;top:0;width:490px;height:282px;background:linear-gradient(135deg,#6a4a12,#d9a93a 45%,#3a2a0c);clip-path:polygon(0 0,100% 0,74% 100%,0 100%)}
.hero-text{position:absolute;left:493px;top:97px;color:var(--gold);font-weight:300;line-height:1.05}
.hero-text .l1{font-size:31px}
.hero-text .l2{font-size:38px}
.pager{left:508px;top:415px;display:flex;gap:5px}
.pager i{width:6px;height:6px;border-radius:50%;background:var(--charcoal)}
.pager i.on{background:var(--gold);box-shadow:0 0 0 1px var(--charcoal)}
.group-head{height:28px;background:var(--gold);font-size:11.5px;font-weight:600;text-align:center;line-height:28px;color:var(--ink)}
.card{width:172px;top:470px}
.card .photo{margin:0 7px;height:191px;border-left:3px solid var(--gold);border-right:3px solid var(--gold);background:radial-gradient(ellipse 34% 46% at 50% 50%,var(--brass) 0%,var(--brass-light) 45%,var(--white) 100%)}
.card .name{height:26px;background:var(--charcoal);color:var(--gold);text-align:center;line-height:26px;font-size:11.5px}
.card .buy{margin:3px 7px 0;height:22px;background:var(--gold);display:flex;font-size:9px;line-height:22px}
.card .buy span{flex:1;text-align:center}
.card .buy span+span{border-left:1px solid var(--gold-dark)}
.rule{left:177px;width:714px;height:1px;background:var(--rule)}
.popular{left:0;width:1068px;top:746px;text-align:center;font-size:19px;font-weight:300;color:var(--charcoal)}
.icons{left:204px;top:782px;display:flex;gap:30px}
.icons span{width:74px;height:66px;background:radial-gradient(ellipse 45% 48% at 50% 50%,var(--icon) 0%,rgba(107,107,107,.55) 45%,rgba(107,107,107,0) 100%)}
.col-title{font-size:11.5px;font-weight:400;color:var(--ink)}
.about{left:177px;top:896px;width:344px;font-size:8.6px;color:var(--muted);line-height:11.6px;text-align:justify}
.news{left:547px;top:896px;width:344px;font-size:8.6px;line-height:11.6px;color:var(--muted)}
.news .date{color:var(--green);margin-top:7px}
.news a{color:var(--red);text-decoration:underline}
.dots-small{font-size:8px;color:var(--gold);letter-spacing:3px}
.footer{left:162px;width:744px;text-align:center;font-size:7.5px;color:var(--ink)}
.footer a{color:var(--link);text-decoration:none}
.cards{display:flex;justify-content:center;gap:2px}
.cards i{width:22px;height:14px;border:1px solid #ccc;background:#e6e6e6}
.flinks span{margin:0 8px}
</style>
</head>
<body>
<div class="page"></div>

<div class="abs account-links">My account &nbsp;|&nbsp; My wishlist</div>
<div class="abs brand"><span class="brand-mark"></span><span class="brand-name">CREST HORN</span></div>
<div class="abs pill pill-post">
  <svg width="10" height="7" viewBox="0 0 10 7"><rect x="0" y="0" width="6" height="5" fill="#222"/><rect x="6" y="2" width="4" height="3" fill="#222"/><circle cx="2" cy="6" r="1" fill="#222"/><circle cx="8" cy="6" r="1" fill="#222"/></svg>
  FREE POSTAGE ON ORDERS OVER $50</div>
<div class="abs pill pill-gift">
  <svg width="8" height="8" viewBox="0 0 8 8"><rect x="0" y="2" width="8" height="6" fill="#222"/><rect x="3.5" y="2" width="1" height="6" fill="#f6c23b"/></svg>
  FREE GIFT WRAPPING</div>
<div class="abs search">FIND A PRODUCT OR BRAND
  <span class="search-btn"><svg width="26" height="21" viewBox="0 0 26 21"><circle cx="11" cy="9" r="4" fill="none" stroke="#222" stroke-width="2"/><line x1="14" y1="12" x2="18" y2="16" stroke="#222" stroke-width="2.5"/></svg></span></div>
<div class="abs cart"><svg width="10" height="9" viewBox="0 0 10 9"><path d="M0 1h2l1.5 5h5L10 2H3" fill="none" stroke="#222" stroke-width="1.2"/><circle cx="4" cy="8" r="1" fill="#222"/><circle cx="8" cy="8" r="1" fill="#222"/></svg>$0.00 (<b>0</b>)</div>
<div class="abs bag">MY BAG</div>

<nav class="abs nav">
  <a>HOME</a><a>ABOUT</a><a>INSTUMENTS</a><a>TRADE IN YOUR INSTRUMENT</a><a>SELL YOUR INSTRUMENT</a><a>FAQ'S</a><a style="border:0">CONTACT US</a>
  <span class="social"><i class="dot-icon"></i><i class="dot-icon"></i><i class="dot-icon"></i></span>
</nav>

<section class="abs hero">
  <div class="hero-photo" role="img" aria-label="Close-up photo of a brass saxophone's keys and bell"></div>
  <div class="hero-text"><div class="l1">Buy used band</div><div class="l2">instruments</div></div>
</section>
<div class="abs pager"><i></i><i></i><i class="on"></i><i></i><i></i></div>

<div class="abs group-head" style="left:171px;top:442px;width:355px">BARITONE</div>
<div class="abs group-head" style="left:540px;top:442px;width:357px">ALTO SAX</div>

<div class="abs card" style="left:171px"><div class="photo" role="img" aria-label="Photo of a brass baritone horn"></div><div class="name">BARITONE 01</div><div class="buy"><span>ADD TO CART</span><span>$599.99</span></div></div>
<div class="abs card" style="left:354px"><div class="photo" role="img" aria-label="Photo of a brass baritone horn"></div><div class="name">BARITONE 02</div><div class="buy"><span>ADD TO CART</span><span>$599.99</span></div></div>
<div class="abs card" style="left:540px"><div class="photo" role="img" aria-label="Photo of a gold alto saxophone"></div><div class="name">ALTO SAX 01</div><div class="buy"><span>ADD TO CART</span><span>$599.99</span></div></div>
<div class="abs card" style="left:725px"><div class="photo" role="img" aria-label="Photo of a straight gold saxophone"></div><div class="name">ALTO SAX 02</div><div class="buy"><span>ADD TO CART</span><span>$599.99</span></div></div>

<div class="abs rule" style="top:732px"></div>
<h2 class="abs popular">OUR POPULAR PRODUCTS</h2>
<div class="abs icons">
  <span role="img" aria-label="Alto sax silhouette"></span>
  <span role="img" aria-label="Trumpet silhouette"></span>
  <span role="img" aria-label="Flute silhouette"></span>
  <span role="img" aria-label="Clarinet silhouette"></span>
  <span role="img" aria-label="Trombone silhouette"></span>
  <span role="img" aria-label="Tenor sax silhouette"></span>
  <span role="img" aria-label="Baritone silhouette"></span>
</div>
<div class="abs rule" style="top:878px"></div>

<div class="abs about">
  <h3 class="col-title">ABOUT CREST HORN INSTRUMENTS</h3>
  <p style="margin-top:13px">A company in the San Jose/SF Bay area that showcases the financial benefits of buying used band instruments for junior high students.This would be opposed to the current and costly option of renting cheap quality instruments from the 2 or 3 local music stores that charge a monthly fee that over the years charges the buyer 3 or 4x over..</p>
  <p style="margin-top:11px">We target middle schools are Larkfield Middle School and Maple Middle School in San Jose, CA. Both have award winning band programs.</p>
  <div class="dots-small" style="text-align:center;margin-top:14px">•••••••</div>
</div>
<div class="abs news">
  <h3 class="col-title">LATEST NEWS</h3>
  <div class="date" style="margin-top:13px">02/20/2014</div>
  <div>Lorem Ipsum is simply dummy text of the printing and typesetting industry. Lorem...</div>
  <a>Read more</a>
  <div class="date">02/20/2014</div>
  <div>Lorem Ipsum is simply dummy text of the printing and typesetting industry. Lorem...</div>
  <a>Read more</a>
  <div class="dots-small" style="text-align:center;margin-top:14px">•••••••</div>
</div>

<div class="abs rule" style="top:1038px"></div>
<div class="abs footer" style="top:1055px"><i class="dot-icon"></i> &nbsp; <i class="dot-icon"></i> &nbsp; <i class="dot-icon"></i></div>
<div class="abs footer" style="top:1078px">Call 0198 7654 321 or email <a>contact@cresthornsupply.com</a></div>
<div class="abs footer cards" style="top:1099px"><i></i><i></i><i></i><i></i><i></i><i></i><i></i><i></i><i></i></div>
<div class="abs footer flinks" style="top:1129px"><span>Home</span>|<span>About</span>|<span>Instuments</span>|<span>Trade in your instrument</span>|<span>Sell your instrument</span>|<span>FAQ's</span>|<span>Contact Us</span></div>
<div class="abs footer" style="top:1149px">Copyright 2014 Crest Horn Instruments</div>
</body>
</html>
```